Counseling Practice Business Card

I need a professional looking business card incorporating my new logo that was just completed. Card needs to incorporate my name and title, description of my specialty, my address, my phone number, my fax number, my email and my website URL. I need to be able to choose design on/with different paper colors and textures.
I do not have a lot of business card ideas so I am open to anything but I want bold,sharp, clear card without additional designs other than my logo (see attached file info). I am open to different color backgrounds or paper colors including black. I do not like traditional brackets around area codes in phone number or dashes between numbers in phone number. Am open to other ways of presenting including periods between numbers as appropriate. I do not know enough to know what I like yet but I want card to coordinate and work together with my logo. My practice emphasizes natural mental health interventions so any use of color (with background paper color or the blue and green in my logo) that elicits nature is nice. In addition to black, any natural brown or wood looking background might be desirable also. Most of the offerings so far look very similar and boring.

Target Market(s)

Potential therapy clients and other professionals

Contact Information for Business Card

Card information:
Gerald M. Whitcombe, Ph.D.
Licensed Clinical Psychologist
Integrative Health Coach
4812 Marlowe Ridge Blvd SE
Suite 310
Duluth, GA 30096
(770) 415-2983 phone
(770) 581-4096 fax
drgeraldwhitcombe@quillmarsh.net
brightfernwellness.net

Font styles to use
Serif
Sans Serif
Other font styles liked:
• anything that you think looks crisp, clear and easily readable

Requirements
Must have
• Any color used should coordinate with my logo design (see attached files).
• Card should be printed horizontally so top and bottom are longest sides of rectangle.
• Background color or paper color should complement and highlight logo. Do not like a white background. black, grey, brown or any color my logo would blend well with.
Nice to have
• I would like designer to utilize color to highlight letters/name or phone-fax-web symbols.
• Bottom edge of card could be highlighted if appropriate to an idea.
Should not have
• I would NOT want the card to have a pure white background at all.
• No clear cards.
• Cards should be oriented with long sides on bottom and top, NOT sides. DO NOT LIKE THIS THIN TALL ORIENTATION.

```html
<!DOCTYPE html>
<html lang="en">
<head>
<meta charset="utf-8">
<title>Brightfern Wellness – Business Card</title>
<link rel="stylesheet" href="https://fonts.googleapis.com/css2?family=Open+Sans:wght@400;600&display=swap">
<style>
  :root {
    --stage: #2c2c2e;
    --card: #1d1e20;
    --card-back: #202123;
    --pattern-tone: #26272a;
    --blue: #2b7cc4;
    --green: #1f8a44;
    --text: #dcdcdc;
    --rule: #3a3b3e;
    --white: #ffffff;
  }
  * { box-sizing: border-box; margin: 0; padding: 0; }
  html, body { width: 1200px; height: 1108px; overflow: hidden; }
  body {
    background: var(--stage);
    font-family: "Open Sans", Arial, sans-serif;
    position: relative;
  }
  .card {
    position: absolute;
    left: 160px;
    width: 880px;
    height: 500px;
    border-radius: 24px;
    overflow: hidden;
  }
  .card--front {
    top: 40px;
    background: var(--card);
    display: flex;
    align-items: center;
  }
  .card--back { top: 568px; background: var(--card-back); }

  .front-brand {
    width: 400px;
    text-align: center;
    font-size: 46px;
    font-weight: 600;
    color: var(--blue);
    letter-spacing: 0.5px;
    line-height: 1.1;
  }
  .details {
    width: 460px;
    display: flex;
    flex-direction: column;
    align-items: center;
    text-align: center;
  }
  .identity .name {
    font-size: 21px;
    font-weight: 600;
    color: var(--blue);
    text-transform: uppercase;
    letter-spacing: 0.5px;
    white-space: nowrap;
  }
  .identity .name .degree { color: var(--green); }
  .identity .title {
    margin-top: 6px;
    font-size: 18px;
    color: var(--text);
    line-height: 1.4;
  }
  .rule {
    width: 320px;
    height: 1px;
    margin: 18px 0;
    background: var(--rule);
  }
  .contact, .address {
    font-size: 18px;
    color: var(--text);
    line-height: 1.45;
    white-space: nowrap;
  }
  .contact .label { color: var(--blue); font-weight: 600; }
  .contact .web { color: var(--green); }

  .back-pattern {
    position: absolute;
    inset: 0;
    background: linear-gradient(160deg, var(--pattern-tone), var(--card-back) 70%);
  }
  .back-brand {
    position: absolute;
    top: 50%;
    left: 0;
    width: 100%;
    transform: translateY(-50%);
    text-align: center;
    font-size: 54px;
    font-weight: 600;
    color: var(--white);
    line-height: 1.1;
  }
</style>
</head>
<body>
  <section class="card card--front">
    <div class="front-brand">Brightfern<br>Wellness</div>
    <div class="details">
      <div class="identity">
        <p class="name">Gerald M. Whitcombe, <span class="degree">Ph.D.</span></p>
        <p class="title">Licensed Clinical Psychologist /<br>Integrative Health Coach</p>
      </div>
      <div class="rule"></div>
      <div class="contact">
        <p><span class="label">P:</span> 770. 415.2983</p>
        <p><span class="label">F:</span> 770. 581.4096</p>
        <p><span class="label">E:</span> drgeraldwhitcombe@quillmarsh.net</p>
        <p class="web">www.brightfernwellness.net</p>
      </div>
      <div class="rule"></div>
      <div class="address">
        <p>4812 Marlowe Ridge Blvd SE</p>
        <p>Suite 310 Duluth, GA 30096</p>
      </div>
    </div>
  </section>

  <section class="card card--back">
    <div class="back-pattern" role="img" aria-label="Faint tone-on-tone repeated brand background"></div>
    <div class="back-brand">Brightfern<br>Wellness</div>
  </section>
</body>
</html>
```